National Mission Critical Construction Contractor needs Stationery Design to make a bold statement

We are a small commercial construction company, working primarily in mission critical facilities across the U.S.. We have exciting corporate changes going an and a new logo and office space so we need new stationery. The final design should incorporate our new logo and invoke a fresh, high-tech feel while looking simple and modern.

Industry/Entity Type

Construction

Contact Information for Business Card

We are required to list our state licensing qualifications on the back of our card.

Font styles to use
Sans Serif

Requirements
Must have
• We need to have a design for second page of stationery, envelopes both standard and with a window and for a 3 x 4 notepad.

```html
<!DOCTYPE html>
<html lang="en">
<head>
<meta charset="utf-8">
<title>Northgate Stationery</title>
<link href="https://fonts.googleapis.com/css2?family=Montserrat:wght@400;600;700&display=swap" rel="stylesheet">
<style>
  :root{
    --brand-blue:#0b72b9;
    --brand-green:#8cc63f;
    --paper:#ffffff;
    --backdrop:#c3c4c6;
    --shadow:rgba(0,0,0,.35);
  }
  html,body{margin:0;padding:0;overflow:hidden;}
  body{width:1200px;height:927px;background:var(--backdrop);position:relative;font-family:'Montserrat',sans-serif;}
  .sheet{position:absolute;box-shadow:6px 8px 12px var(--shadow);}

  .letterhead{left:149px;top:48px;width:441px;height:568px;background:var(--paper);}
  .letterhead-header{position:absolute;left:0;top:0;width:100%;height:88px;background:var(--brand-blue);border-bottom:8px solid var(--brand-green);}
  .brand{position:absolute;display:flex;align-items:center;gap:10px;}
  .brand-mark{border-radius:50%;box-sizing:border-box;flex:none;}
  .brand-name{font-weight:600;letter-spacing:.5px;}
  .letterhead .brand{left:16px;top:17px;}
  .letterhead .brand-mark{width:58px;height:58px;border:3px solid var(--paper);}
  .letterhead .brand-name{color:var(--paper);font-size:22px;}
  .contact{position:absolute;right:16px;top:15px;text-align:right;color:var(--paper);font-size:10px;line-height:12px;font-style:normal;}
  .contact .gap{height:4px;}
  .contact-line{display:flex;justify-content:flex-end;align-items:center;gap:6px;}
  .contact-line svg{width:7px;height:7px;flex:none;}
  .contact b{font-weight:700;}

  .folder{left:610px;top:48px;width:440px;height:568px;background:var(--brand-blue);}
  .emblem{position:absolute;left:50%;transform:translateX(-50%);display:flex;flex-direction:column;align-items:center;}
  .emblem-ring{border-radius:50%;border:solid var(--paper);box-sizing:border-box;}
  .emblem-name{color:var(--paper);font-weight:600;letter-spacing:1px;}
  .folder .emblem{top:182px;}
  .folder .emblem-ring{width:206px;height:206px;border-width:5px;}
  .folder .emblem-name{font-size:20px;margin-top:16px;}
  .web{position:absolute;left:0;width:100%;text-align:center;color:var(--paper);font-size:12px;}
  .web b{font-weight:700;}
  .folder .web{top:526px;}

  .envelope-front{left:135px;top:643px;width:455px;height:235px;background:var(--paper);}
  .envelope-front-band{position:absolute;left:0;top:0;width:100%;height:30px;background:var(--brand-blue);border-radius:16px 16px 0 0;}
  .envelope-front .brand{left:107px;top:102px;}
  .envelope-front .brand-mark{width:58px;height:58px;border:3px solid var(--brand-blue);}
  .envelope-front .brand-name{color:var(--brand-blue);font-size:22px;}
  .return-address{position:absolute;left:0;width:100%;top:214px;text-align:center;color:var(--brand-blue);font-size:9.5px;}

  .envelope-back{left:610px;top:671px;width:455px;height:207px;background:var(--brand-blue);}
  .envelope-back-flap{position:absolute;left:0;top:0;width:100%;height:30px;background:var(--brand-green);border-radius:0 0 16px 0;}
  .envelope-back .emblem{top:72px;}
  .envelope-back .emblem-ring{width:88px;height:88px;border-width:3px;}
  .envelope-back .emblem-name{display:none;}
  .envelope-back .web{top:182px;}
</style>
</head>
<body>

<section class="sheet letterhead">
  <header class="letterhead-header">
    <div class="brand">
      <span class="brand-mark"></span>
      <span class="brand-name">NORTHGATE</span>
    </div>
    <address class="contact">
      <div>418B W. Cedar Ridge Ave.</div>
      <div>Lakeview, TX. 77510</div>
      <div class="gap"></div>
      <div class="contact-line"><span>+1.555.204.3187</span>
        <svg viewBox="0 0 10 10"><path d="M2 1l2 2-1 1.5a6 6 0 0 0 2.5 2.5L7 6l2 2-1.5 1.5C4 9 1 6 0.5 2.5z" fill="var(--brand-green)"/></svg></div>
      <div class="contact-line"><span>info@northgatecm.com</span>
        <svg viewBox="0 0 10 10"><rect x="0.5" y="2" width="9" height="6" fill="none" stroke="var(--brand-green)"/><path d="M0.5 2l4.5 3.5L9.5 2" fill="none" stroke="var(--brand-green)"/></svg></div>
      <div class="contact-line"><span>www.<b>northgatecm</b>.com</span>
        <svg viewBox="0 0 10 10"><circle cx="5" cy="5" r="4.5" fill="var(--brand-green)"/></svg></div>
    </address>
  </header>
</section>

<section class="sheet folder">
  <div class="emblem">
    <span class="emblem-ring"></span>
    <span class="emblem-name">NORTHGATE</span>
  </div>
  <div class="web">www.<b>northgatecm</b>.com</div>
</section>

<section class="sheet envelope-front">
  <div class="envelope-front-band"></div>
  <div class="brand">
    <span class="brand-mark"></span>
    <span class="brand-name">NORTHGATE</span>
  </div>
  <div class="return-address">418B W. Cedar Ridge Ave. Lakeview, TX. 77510</div>
</section>

<section class="sheet envelope-back">
  <div class="envelope-back-flap"></div>
  <div class="emblem">
    <span class="emblem-ring"></span>
    <span class="emblem-name">NORTHGATE</span>
  </div>
  <div class="web">www.<b>northgatecm</b>.com</div>
</section>

</body>
</html>
```